business card for a massage therapy practice named 'Cedar and Willow Massage Studio'

I really need a trendy, yet easy on the eyes business card to complement my logo. Ideally with some gold or rose gold foil work.

My uploaded file of the logo I have in horizontal but I have a vertical version as well. Another color that is used in the website is a blush pink here and there. I'd like to see some trendy tropical leaves in the design.

```html
<!DOCTYPE html>
<html lang="en">
<head>
<meta charset="utf-8">
<title>Cedar and Willow Massage Studio – Business Card</title>
<link rel="stylesheet" href="https://fonts.googleapis.com/css2?family=Lora:wght@400;500&family=Parisienne&display=swap">
<style>
  :root {
    --stage: #3d3630;
    --blush-light: #fbeee8;
    --blush: #f5d3c6;
    --blush-deep: #efc1b0;
    --ink: #23201f;
    --gold: #b39c6b;
    --teal: #1bb3ac;
    --teal-soft: #6fcbb8;
    --teal-line: #8fd6c4;
    --forest: #4d8678;
    --name-green: #3f7268;
    --paper: #ffffff;
  }
  * { box-sizing: border-box; margin: 0; padding: 0; }
  html, body { width: 1200px; height: 1200px; overflow: hidden; }
  body {
    background: var(--stage);
    font-family: "Lora", Georgia, serif;
    position: relative;
  }
  .card {
    position: absolute;
    left: 170px;
    width: 860px;
    height: 491px;
    overflow: hidden;
    box-shadow: 0 10px 30px rgba(0,0,0,.35);
  }
  .card--front { top: 70px; }
  .card--back { top: 640px; background: var(--paper); }

  .watercolor {
    position: absolute; inset: 0;
    background:
      radial-gradient(ellipse 45% 40% at 55% 50%, var(--blush-deep), transparent 70%),
      radial-gradient(ellipse 60% 55% at 30% 65%, var(--blush), transparent 75%),
      radial-gradient(ellipse 50% 45% at 80% 30%, var(--blush), transparent 75%),
      var(--blush-light);
  }
  .brand {
    position: absolute;
    display: flex; align-items: center; gap: 22px;
    color: var(--ink);
    font-weight: 400;
  }
  .brand__dot {
    width: 34px; height: 34px; border-radius: 50%;
    background: var(--gold); flex: none;
  }
  .card--front .brand {
    left: 0; right: 0; top: 0; bottom: 0;
    justify-content: center;
    font-size: 40px;
  }
  .brand__name { line-height: 1.15; text-align: left; }

  .wave { position: absolute; inset: 0; }
  .card--back .brand {
    left: 60px; top: 150px;
    font-size: 34px;
  }
  .holder {
    position: absolute; right: 60px; top: 40px;
    text-align: right; color: var(--name-green);
  }
  .holder__name { font-family: "Parisienne", cursive; font-size: 58px; line-height: 1; }
  .holder__role { font-size: 20px; color: var(--ink); margin-top: -4px; }

  .contact {
    position: absolute; right: 44px; top: 250px;
    list-style: none; color: var(--paper);
    font-size: 21px; text-align: right;
  }
  .contact li {
    display: flex; justify-content: flex-end; align-items: center;
    gap: 12px; margin-bottom: 10px;
  }
  .contact li.contact__address {
    border-top: 1px solid rgba(255,255,255,.6);
    padding-top: 10px;
  }
  .contact svg { width: 18px; height: 18px; flex: none; }
</style>
</head>
<body>

<section class="card card--front" aria-label="Card front">
  <div class="watercolor"></div>
  <div class="brand">
    <span class="brand__dot"></span>
    <span class="brand__name">Cedar and Willow<br>Massage Studio</span>
  </div>
</section>

<section class="card card--back" aria-label="Card back">
  <svg class="wave" viewBox="0 0 860 491" preserveAspectRatio="none" aria-hidden="true">
    <defs>
      <linearGradient id="teal-fade" x1="0" y1="1" x2="1" y2="0">
        <stop offset="0" stop-color="var(--teal-soft)"/>
        <stop offset="1" stop-color="var(--teal)"/>
      </linearGradient>
    </defs>
    <path d="M0,345 C250,430 460,340 570,230 C650,150 730,118 860,112 L860,491 L0,491 Z" fill="url(#teal-fade)"/>
    <path d="M0,318 C250,400 450,320 560,210 C600,170 620,150 640,140" fill="none" stroke="var(--forest)" stroke-width="9"/>
    <path d="M0,335 C250,418 455,330 565,220 C645,140 730,100 860,96" fill="none" stroke="var(--teal-line)" stroke-width="3"/>
  </svg>

  <div class="holder">
    <div class="holder__name">Maya Linden</div>
    <div class="holder__role">Director</div>
  </div>

  <div class="brand">
    <span class="brand__dot"></span>
    <span class="brand__name">Cedar and Willow<br>Massage Studio</span>
  </div>

  <ul class="contact">
    <li>1-555-014-2270
      <svg viewBox="0 0 24 24"><path fill="#fff" d="M6.6 10.8a15 15 0 006.6 6.6l2.2-2.2c.3-.3.7-.4 1-.2 1.1.4 2.3.6 3.6.6.6 0 1 .4 1 1V20c0 .6-.4 1-1 1A17 17 0 013 4c0-.6.4-1 1-1h3.5c.6 0 1 .4 1 1 0 1.3.2 2.5.6 3.6.1.3 0 .7-.2 1z"/></svg>
    </li>
    <li>maya@cedarandwillow.com
      <svg viewBox="0 0 24 24"><rect x="2" y="5" width="20" height="14" rx="1" fill="#fff"/><path d="M2 6l10 7 10-7" fill="none" stroke="var(--teal)" stroke-width="1.6"/></svg>
    </li>
    <li>www.cedarandwillow.com
      <svg viewBox="0 0 24 24"><circle cx="12" cy="12" r="9" fill="none" stroke="#fff" stroke-width="2"/><path d="M3 12h18M12 3c3 3 3 15 0 18M12 3c-3 3-3 15 0 18" fill="none" stroke="#fff" stroke-width="1.5"/></svg>
    </li>
    <li class="contact__address">Harbor City, Coastland
      <svg viewBox="0 0 24 24"><path fill="#fff" d="M12 2a7 7 0 00-7 7c0 5 7 13 7 13s7-8 7-13a7 7 0 00-7-7zm0 9.5A2.5 2.5 0 1112 6.5a2.5 2.5 0 010 5z"/></svg>
    </li>
  </ul>
</section>

</body>
</html>
```